Glen Whitmore Professional Coaching

I would like a website with a mountain theme geared towards professional executives reaching higher peaks and goals. This is a 3 page website with brand essence information on the opening page, the coaching process on a second page and "about me" and lead capture form on a third page

Target Market(s)

C-Level audience, involved in tech, government, manufacturing, and transportation type of corporations

Coding

Coded - Design and coding required

Number of Pages Required

3 page

Font styles to use
Sans Serif

Colors
a7a7a7
1b1b1b
e8e8e8
3176b5
abd036
0355a3

Requirements
Must have
• Looking for a user friendly site that I can manage/update going forward. Must have:
• 1. "Is coaching right for you?" - page 1
• 2. "Our Process" page 2 - I will describe how we approach coaching
• 3. "Contact us" page 3 where I can capture contact information from potential clients
• 4. Clean and professional with more modern font
• 5. Links to personal social media sites
• 6. Ability to upload/download .pdf documents as resources
• 7. Ability to add on new pages in the future (such as a blog page)
Nice to have
• I want a place to store articles I write or use.
• LinkedIn or Summitly Feed
Should not have
• Not fluffy or too 'zen' like personal life coaches tend to present.

```html
<!DOCTYPE html>
<html lang="en">
<head>
<meta charset="utf-8">
<title>Glen Whitmore Professional Coaching</title>
<link rel="stylesheet" href="https://fonts.googleapis.com/css2?family=Montserrat:wght@300;400;500;700&family=Open+Sans:wght@400;600&display=swap">
<style>
:root{
  --navy:#0b2150;
  --brand:#0d2a5c;
  --royal:#0e3f86;
  --footer:#0b3f87;
  --cyan:#2ed4e8;
  --ink:#222;
  --muted:#555;
  --mist:#eef0f8;
  --line:#b9bcc4;
  --white:#fff;
}
*{margin:0;padding:0;box-sizing:border-box}
html,body{width:781px;height:1200px;overflow:hidden;background:var(--white)}
body{position:relative;font-family:"Open Sans",Arial,sans-serif;color:var(--ink)}
.abs{position:absolute}
.hero{left:0;top:0;width:781px;height:426px;background:linear-gradient(160deg,#e9e9e9 0%,#cfcfcf 35%,#f0f0f0 55%,#bdbdbd 80%,#dcdcdc 100%)}
.brand{left:94px;top:4px;font-family:Montserrat,sans-serif;font-weight:700;font-size:32px;color:var(--brand);letter-spacing:-.3px}
.nav{right:94px;top:15px;display:flex;gap:25px;font-family:Montserrat,sans-serif;font-size:10px;color:#333}
.nav a{color:inherit;text-decoration:none}
.nav .active{color:var(--brand);text-decoration:underline;text-underline-offset:3px}
.portrait{left:486px;top:60px;width:200px;height:366px;background:linear-gradient(180deg,#c9c4c0 0%,#6f7a92 25%,#2b3a5e 45%,#1d2740 100%)}
.hero-title{left:91px;top:115px;font-family:Montserrat,sans-serif;font-weight:300;font-size:30.5px;color:#2b2b2b;white-space:nowrap}
.hero-text{left:94px;top:161px;width:340px;font-size:11px;line-height:17.6px;color:var(--ink)}
.btn{display:flex;align-items:center;justify-content:center;background:var(--royal);color:var(--white);font-family:Montserrat,sans-serif;font-size:11px;font-weight:500;text-decoration:none}
.hero-btn{left:94px;top:224px;width:84px;height:28px}
.quote-band{left:0;top:317px;width:535px;height:109px;background:var(--navy)}
.quote{left:94px;top:334px;width:430px;font-family:Montserrat,sans-serif;font-size:12.5px;line-height:18px;color:var(--white)}
.quote-by{left:94px;top:376px;font-family:Montserrat,sans-serif;font-weight:700;font-size:8.5px;color:var(--cyan)}
.dots{left:94px;top:401px;display:flex;gap:9.5px}
.dots span{width:6px;height:6px;background:#5b6f9a}
.dots .on{background:var(--white)}
.process{left:0;top:426px;width:781px;height:375px;background:var(--mist)}
.summit{left:0;top:630px;width:781px;height:171px;background:linear-gradient(180deg,var(--mist) 0%,#d3deec 35%,#dfe6ef 65%,#c9beb6 100%)}
.section-title{left:0;width:781px;text-align:center;font-family:Montserrat,sans-serif;font-weight:500;font-size:21px;color:var(--brand)}
.step{top:509px;width:190px;text-align:center}
.step .icon{width:78px;height:62px;margin:0 auto;background:var(--white);display:flex;align-items:center;justify-content:center}
.step h3{margin-top:10px;font-family:Montserrat,sans-serif;font-weight:500;font-size:11px;color:var(--brand)}
.step p{margin-top:3px;font-size:6.8px;line-height:11px;color:var(--muted)}
.field{background:var(--white);border:1px solid var(--line);font-size:7.5px;color:#777;padding:9px 10px}
.ridge{left:90px;top:1055px;width:600px;height:75px;background:linear-gradient(180deg,#ffffff 0%,#e4e4e4 45%,#b3b0ac 100%)}
.footer{left:0;top:1130px;width:781px;height:70px;background:var(--footer);color:var(--white)}
.foot-links{left:94px;top:1149px;font-size:7.5px;color:var(--white)}
.foot-links span{margin:0 6px}
.copy{left:94px;top:1169px;font-size:7.5px;color:var(--white)}
.social{right:94px;top:1159px;display:flex;gap:14px;font-family:Montserrat,sans-serif;font-size:8px;font-weight:500;color:var(--white)}
</style>
</head>
<body>
<header>
  <div class="abs hero" role="img" aria-label="Snow-covered mountain range in soft grey tones"></div>
  <div class="abs brand">Glen Whitmore</div>
  <nav class="abs nav"><a class="active" href="#">HOME</a><a href="#">COACHING PROCESS</a><a href="#">ABOUT ME</a></nav>
  <div class="abs portrait" role="img" aria-label="Portrait of the coach in a navy blazer"></div>
  <h1 class="abs hero-title">Professional Coaching</h1>
  <p class="abs hero-text">Maecenas vel tortor accumsan quam varius imperdiet vel eget elit. Aenean facilisis tincidunt lectus, id dictum nisi luctus eget. Vivamus efficitur ex condimentum, malesuada eros eget.</p>
  <a class="abs btn hero-btn" href="#">Contact Me</a>
  <div class="abs quote-band"></div>
  <blockquote class="abs quote">“ Fusce vitae lectus sit amet mi pulvinar maximus. Aenean placerat, nibh accumsan aliquet, magna nibh accumsan nibh. ”</blockquote>
  <div class="abs quote-by">MARK DALTON, COMPANY NAME</div>
  <div class="abs dots"><span class="on"></span><span></span><span></span><span></span></div>
</header>

<section>
  <div class="abs process"></div>
  <div class="abs summit" role="img" aria-label="Hiker standing on a rocky summit above misty mountains"></div>
  <h2 class="abs section-title" style="top:467px">COACHING PROCESS</h2>
  <div class="abs step" style="left:91px">
    <div class="icon"><svg width="40" height="40" viewBox="0 0 40 40" fill="none" stroke="#0d2a5c" stroke-width="1.6"><rect x="5" y="5" width="24" height="31"/><rect x="12" y="2" width="10" height="5" fill="#fff"/><line x1="10" y1="13" x2="24" y2="13"/><line x1="10" y1="18" x2="24" y2="18"/><line x1="10" y1="23" x2="18" y2="23"/><circle cx="13" cy="30" r="3"/><line x1="34" y1="6" x2="34" y2="34"/></svg></div>
    <h3>Aliquam erat volutpat</h3>
    <p>Quisque aliquet ex nec est vestibulum pulvinar. Pellentes que convallis molestie enim sit amet efficitur. Etiam id imperdiet lectus. Vivamus lacus justo.</p>
  </div>
  <div class="abs step" style="left:295px">
    <div class="icon"><svg width="40" height="40" viewBox="0 0 40 40" fill="none" stroke="#0d2a5c" stroke-width="1.6"><rect x="4" y="4" width="32" height="20"/><line x1="10" y1="11" x2="30" y2="11"/><line x1="10" y1="17" x2="24" y2="17"/><rect x="5" y="29" width="6" height="7"/><rect x="13" y="29" width="6" height="7"/><rect x="21" y="29" width="6" height="7"/><rect x="29" y="29" width="6" height="7"/></svg></div>
    <h3>Cras augue magna</h3>
    <p>Quisque aliquet ex nec est vestibulum pulvinar. Pellentes que convallis molestie enim sit amet efficitur. Etiam id imperdiet lectus. Vivamus lacus justo.</p>
  </div>
  <div class="abs step" style="left:499px">
    <div class="icon"><svg width="40" height="40" viewBox="0 0 40 40" fill="none" stroke="#0d2a5c" stroke-width="1.6"><line x1="4" y1="36" x2="36" y2="36"/><rect x="7" y="29" width="5" height="7"/><rect x="14" y="25" width="5" height="11"/><rect x="21" y="20" width="5" height="16"/><rect x="28" y="14" width="5" height="22"/><polyline points="6,24 18,16 26,12 34,4"/><polyline points="28,4 34,4 34,10"/><line x1="5" y1="6" x2="12" y2="6"/><line x1="5" y1="10" x2="10" y2="10"/></svg></div>
    <h3>Aenean placerat</h3>
    <p>Quisque aliquet ex nec est vestibulum pulvinar. Pellentes que convallis molestie enim sit amet efficitur. Etiam id imperdiet lectus. Vivamus lacus justo.</p>
  </div>
</section>

<section>
  <h2 class="abs section-title" style="top:820px">CONTACT US</h2>
  <div class="abs field" style="left:229px;top:857px;width:156px;height:28px">Name</div>
  <div class="abs field" style="left:395px;top:857px;width:156px;height:28px">Email</div>
  <div class="abs field" style="left:229px;top:899px;width:156px;height:28px">Phone</div>
  <div class="abs field" style="left:395px;top:899px;width:156px;height:28px">Title</div>
  <div class="abs field" style="left:229px;top:940px;width:322px;height:65px">Message</div>
  <a class="abs btn" href="#" style="left:359px;top:1021px;width:62px;height:26px">Submit</a>
  <div class="abs ridge" role="img" aria-label="Snowy mountain peaks"></div>
</section>

<footer>
  <div class="abs footer"></div>
  <div class="abs foot-links">Home<span>|</span>Coaching Process<span>|</span>About Me</div>
  <div class="abs copy">Copyright © 2019 Glen Whitmore. All rights reserved.</div>
  <div class="abs social"><span>Peakbook</span><span>Summitly</span></div>
</footer>
</body>
</html>
```